KRT Info Brochure

We need a brochure design for a new not-for-profit organisation that is aimed at providing homeless people with a residence that also provides counselling and vocational training to assist them to find suitable employment at the end of the program.
PLEASE NOTE:
Brochure to be A4.
I know the brochure is quite long, it is really a booklet, but please note that it does not have to have a lot of work done on it, I just want it to look professional and the front cover and inside page to look good.
Also please leave about 2-3 pages at the end as I will be adding in some architect drawings.
Please add in a last page with Contact written at the bottom - we will fill that in later. So please ensure it is editable in PDF.
Thank you so much.
Cheers
Marta

```html
<!DOCTYPE html>
<html lang="en">
<head>
<meta charset="utf-8">
<title>KRT Info Brochure – Contents and Executive Summary</title>
<link rel="stylesheet" href="https://fonts.googleapis.com/css2?family=Arimo:wght@400;700&display=swap">
<style>
  :root {
    --backdrop: #e6e6e6;
    --paper: #ffffff;
    --olive: #8c8a3c;
    --olive-light: #b5b36a;
    --amber: #f2b230;
    --ink: #2a2a2a;
    --ink-soft: #444444;
    --leader: #9a9a9a;
  }
  * { box-sizing: border-box; margin: 0; padding: 0; }
  html, body {
    width: 1200px; height: 847px; overflow: hidden;
    background: var(--backdrop);
    font-family: "Arimo", Arial, sans-serif;
    color: var(--ink);
  }
  .spread {
    position: absolute; left: 48px; top: 33px;
    width: 1104px; height: 780px;
    display: flex;
    box-shadow: 0 6px 24px rgba(0,0,0,.18);
  }
  .page {
    position: relative; width: 552px; height: 780px;
    background: var(--paper); overflow: hidden;
  }
  .page--left { border-right: 1px solid #d6d6d6; }

  /* Page frame: flat bands with a thin accent rule */
  .band { position: absolute; left: 0; width: 552px; background: var(--olive); }
  .band--top { top: 0; height: 56px; }
  .band--bottom { bottom: 0; height: 48px; }
  .band::after {
    content: ""; position: absolute; left: 0; right: 0; height: 4px; background: var(--amber);
  }
  .band--top::after { bottom: -10px; }
  .band--bottom::after { top: -10px; }
  .band-tab {
    position: absolute; width: 120px; height: 56px; background: var(--olive-light);
  }
  .page--left .band--top .band-tab { right: 0; top: 0; }
  .page--right .band--top .band-tab { left: 0; top: 0; }
  .page--left .band--bottom .band-tab { right: 0; top: 0; height: 48px; }
  .page--right .band--bottom .band-tab { left: 0; top: 0; height: 48px; }

  /* Contents */
  .contents {
    position: absolute; left: 48px; top: 150px; width: 430px;
    font-size: 10px; line-height: 11.6px;
  }
  .contents h2 { font-size: 11px; font-weight: 700; letter-spacing: .3px; margin-bottom: 2px; }
  .contents ol { list-style: none; }
  .toc-item { display: flex; align-items: baseline; }
  .toc-num { width: 34px; flex: none; }
  .toc-item--sub .toc-num { width: 52px; padding-left: 18px; }
  .toc-label { white-space: nowrap; }
  .toc-item--major .toc-label { text-transform: uppercase; }
  .toc-leader { flex: 1; border-bottom: 1px dotted var(--leader); margin-left: 2px; transform: translateY(-2px); }

  /* Executive summary */
  .brand {
    position: absolute; right: 40px; top: 72px;
    display: flex; align-items: center; gap: 6px;
    font-size: 20px; font-weight: 700; color: var(--amber);
  }
  .brand-dot { width: 20px; height: 20px; border-radius: 50%; background: var(--amber); }
  .summary {
    position: absolute; left: 34px; top: 98px; width: 486px;
    font-size: 8.6px; line-height: 11px; color: var(--ink-soft);
  }
  .summary h1 {
    font-size: 19px; font-weight: 700; color: var(--olive); margin-bottom: 6px;
  }
  .summary p { margin-bottom: 8px; }
  .summary p.tight { margin-bottom: 3px; }
  .photo-residents {
    position: absolute; left: 46px; top: 414px; width: 470px; height: 294px;
    background: radial-gradient(ellipse at 50% 55%, #a7a8b4 0%, #b7c2cf 45%, #e9ecef 100%);
    border-radius: 6px;
  }
</style>
</head>
<body>
<main class="spread">

  <section class="page page--left" aria-label="Contents page">
    <div class="band band--top" aria-hidden="true"><span class="band-tab"></span></div>
    <div class="band band--bottom" aria-hidden="true"><span class="band-tab"></span></div>

    <nav class="contents">
      <h2>CONTENTS</h2>
      <ol>
        <li class="toc-item"><span class="toc-label">Executive Summary</span><span class="toc-leader"></span></li>
        <li class="toc-item toc-item--major"><span class="toc-num">1.</span><span class="toc-label">Homelessness</span><span class="toc-leader"></span></li>
        <li class="toc-item toc-item--major"><span class="toc-num">2.</span><span class="toc-label">Program Overview</span><span class="toc-leader"></span></li>
        <li class="toc-item"><span class="toc-num">2.1.</span><span class="toc-label">Physiological</span><span class="toc-leader"></span></li>
        <li class="toc-item"><span class="toc-num">2.2.</span><span class="toc-label">Psychological</span><span class="toc-leader"></span></li>
        <li class="toc-item"><span class="toc-num">2.3.</span><span class="toc-label">Learning/Training</span><span class="toc-leader"></span></li>
        <li class="toc-item"><span class="toc-num">2.4.</span><span class="toc-label">Special Needs</span><span class="toc-leader"></span></li>
        <li class="toc-item"><span class="toc-num">2.5.</span><span class="toc-label">Vocational Education</span><span class="toc-leader"></span></li>
        <li class="toc-item"><span class="toc-num">2.6.</span><span class="toc-label">Fitting back into Society</span><span class="toc-leader"></span></li>
        <li class="toc-item"><span class="toc-num">2.7.</span><span class="toc-label">Outreach / After Care Program</span><span class="toc-leader"></span></li>
        <li class="toc-item"><span class="toc-num">2.8.</span><span class="toc-label">Family Groups</span><span class="toc-leader"></span></li>
        <li class="toc-item"><span class="toc-num">2.9.</span><span class="toc-label">Young People</span><span class="toc-leader"></span></li>
        <li class="toc-item"><span class="toc-num">2.10.</span><span class="toc-label">Older People</span><span class="toc-leader"></span></li>
        <li class="toc-item"><span class="toc-num">2.11.</span><span class="toc-label">Alcohol &amp; Drug Dependencies</span><span class="toc-leader"></span></li>
        <li class="toc-item toc-item--major"><span class="toc-num">3.</span><span class="toc-label">Operations</span><span class="toc-leader"></span></li>
        <li class="toc-item"><span class="toc-num">3.1.</span><span class="toc-label">Management</span><span class="toc-leader"></span></li>
        <li class="toc-item"><span class="toc-num">3.2.</span><span class="toc-label">Business Location</span><span class="toc-leader"></span></li>
        <li class="toc-item"><span class="toc-num">3.3.</span><span class="toc-label">Foundation Management</span><span class="toc-leader"></span></li>
        <li class="toc-item"><span class="toc-num">3.4.</span><span class="toc-label">KRT Staff</span><span class="toc-leader"></span></li>
        <li class="toc-item"><span class="toc-num">3.5.</span><span class="toc-label">Self-Sustainment</span><span class="toc-leader"></span></li>
        <li class="toc-item"><span class="toc-num">3.6.</span><span class="toc-label">Timeframes</span><span class="toc-leader"></span></li>
        <li class="toc-item"><span class="toc-num">3.7.</span><span class="toc-label">Marketing and Publicity</span><span class="toc-leader"></span></li>
        <li class="toc-item toc-item--major"><span class="toc-num">4.</span><span class="toc-label">The Program Practically</span><span class="toc-leader"></span></li>
        <li class="toc-item"><span class="toc-num">4.1.</span><span class="toc-label">Work Task</span><span class="toc-leader"></span></li>
        <li class="toc-item"><span class="toc-num">4.2.</span><span class="toc-label">Snapshot of a day in the Program</span><span class="toc-leader"></span></li>
        <li class="toc-item"><span class="toc-num">4.3.</span><span class="toc-label">Logistics</span><span class="toc-leader"></span></li>
        <li class="toc-item toc-item--major"><span class="toc-num">5.</span><span class="toc-label">The Future</span><span class="toc-leader"></span></li>
        <li class="toc-item"><span class="toc-num">5.1.</span><span class="toc-label">Complimentary Businesses</span><span class="toc-leader"></span></li>
        <li class="toc-item toc-item--sub"><span class="toc-num">5.1.1.</span><span class="toc-label">Phase 1</span><span class="toc-leader"></span></li>
        <li class="toc-item toc-item--sub"><span class="toc-num">5.1.2.</span><span class="toc-label">Phase 2</span><span class="toc-leader"></span></li>
        <li class="toc-item toc-item--sub"><span class="toc-num">5.1.3.</span><span class="toc-label">Phase 3</span><span class="toc-leader"></span></li>
        <li class="toc-item toc-item--sub"><span class="toc-num">5.1.4.</span><span class="toc-label">Phase 4</span><span class="toc-leader"></span></li>
        <li class="toc-item toc-item--sub"><span class="toc-num">5.1.5.</span><span class="toc-label">Phase 5</span><span class="toc-leader"></span></li>
        <li class="toc-item"><span class="toc-num">5.2.</span><span class="toc-label">The Long Term</span><span class="toc-leader"></span></li>
        <li class="toc-item toc-item--major"><span class="toc-num">6.</span><span class="toc-label">The Finances</span><span class="toc-leader"></span></li>
        <li class="toc-item"><span class="toc-num">6.1.</span><span class="toc-label">Funding</span><span class="toc-leader"></span></li>
        <li class="toc-item"><span class="toc-num">6.2.</span><span class="toc-label">Income</span><span class="toc-leader"></span></li>
        <li class="toc-item"><span class="toc-num">6.3.</span><span class="toc-label">Fundraising</span><span class="toc-leader"></span></li>
        <li class="toc-item"><span class="toc-label">Attachment 1: S.W.O.T. analysis</span><span class="toc-leader"></span></li>
        <li class="toc-item"><span class="toc-label">Attachment 2: Learning For Residents</span><span class="toc-leader"></span></li>
      </ol>
    </nav>
  </section>

  <section class="page page--right" aria-label="Executive summary page">
    <div class="band band--top" aria-hidden="true"><span class="band-tab"></span></div>
    <div class="band band--bottom" aria-hidden="true"><span class="band-tab"></span></div>

    <div class="brand"><span class="brand-dot"></span>KRT</div>

    <article class="summary">
      <h1>Executive Summary</h1>
      <p>KRT Legacy Foundation (KRT) is a not-for-profit organisation that will attempt to break the cycle of homelessness. KRT will provide a live-in residence for homeless people from all age ranges and provide psychological counselling to address the issues associated with the reasons for, and impact of homelessness.</p>
      <p>It is expected that most 'Residents' will require on average twelve months in residence to address their psychological issues, during this time the Resident will be also provided with various types of training, from life-skills to specific vocational education to assist them to move towards independent living.</p>
      <p>Once the Resident is ready, KRT staff will assist the Resident with all aspects of transitioning to independent living and provide on-going assistance and support for as long as is required.</p>
      <p>KRT will cater for family groups and single parents, providing counselling for the entire family group and training for the parent. During the residency the children will attend a local school to reduce the impact to their education.</p>
      <p>KRT recognises that the cost of running the facility and providing training and work experience to a reasonably large group of people in todays economic environment will be challenging. As such, KRT is seeking funding for the initial establishment of the facility, but aims to introduce a number of separate complimentary business entities that will provide the necessary training avenue and income required with the aim of eventually being self-sustaining.</p>
      <p>Overall, KRT aims to reduce the overall incidence of homelessness Australia wide.</p>
      <p class="tight">Residents = homeless people living at KRT complex</p>
      <p>Clients = Residents who have been through the Program and returned to independent living, but remain in the After Care program.</p>
    </article>

    <div class="photo-residents" role="img" aria-label="Photo of a cheerful group of young people giving thumbs up"></div>
  </section>

</main>
</body>
</html>
```